Business Card for Multi-Brand Sportswear Company

We are looking for a business card which represents our company and the multiple brands within it.

The company: Fen Athletics (LTD)
The brands: Fen, TavaPuni, ElmStretch, Grit and Rain

Employees using these cards would be representing Fen Athletics, rather than any of the individual brands. You will see a current design within the uploaded files, to give some inspiration. The actual text of the brands is not necessary, but the logos should be on there is some format.

Our creative minds on this are stretched, so we are looking for someone to make this their own, and show us what a good business card should look like.

We may like to get these printed with spot gloss, so keep that in mind with your designs.

www.fenathletics.co.uk

Industry/Entity Type

Business

Contact Information for Business Card

Leo Pemberton-Hale
Operations Manager
(+44) 1632 960 418
Leo@fenathletics.co.uk
www.fenathletics.co.uk

Font styles to use
Sans Serif
Other font styles liked:
• Eurostile

Colors
ffffff

Requirements
Nice to have
• Dark (black) background

```html
<!DOCTYPE html>
<html lang="en">
<head>
<meta charset="utf-8">
<title>Fen Athletics – Business Card</title>
<link rel="stylesheet" href="https://fonts.googleapis.com/css2?family=Source+Sans+3:ital,wght@0,400;0,600;0,700;1,400&display=swap">
<style>
  :root {
    --backdrop: #555658;
    --card-white: #ffffff;
    --card-black: #000000;
    --ink: #1a1a1a;
    --ink-soft: #6a6a6a;
    --accent-red: #e3202a;
    --divider: #cfcfcf;
    --brand-grey: #8e8e8e;
    --brand-violet: #5e5866;
    --brand-red: #d8262c;
  }
  * { box-sizing: border-box; margin: 0; padding: 0; }
  html, body {
    width: 1105px; height: 1200px; overflow: hidden;
    background: var(--backdrop);
    font-family: "Source Sans 3", sans-serif;
  }
  .card {
    position: absolute; left: 196px; width: 720px; height: 412px;
  }
  .card--front { top: 146px; background: var(--card-white); }
  .card--back { top: 602px; background: var(--card-black); }

  .company-mark {
    position: absolute; left: 58px; top: 192px;
    display: flex; align-items: center; gap: 12px;
  }
  .company-mark__square { width: 22px; height: 22px; background: var(--accent-red); }
  .company-mark__name { font-size: 34px; font-weight: 700; color: var(--ink); letter-spacing: -0.5px; }

  .divider {
    position: absolute; left: 385px; top: 98px; width: 1px; height: 210px;
    background: var(--divider);
  }
  .contact { position: absolute; left: 419px; top: 100px; }
  .contact__name { font-size: 26px; font-weight: 700; color: var(--accent-red); line-height: 1.1; }
  .contact__role { font-size: 20px; color: var(--ink); margin-top: 2px; }
  .contact__address { font-size: 19px; color: var(--ink-soft); margin-top: 14px; line-height: 1.35; }
  .contact__lines { list-style: none; margin-top: 10px; }
  .contact__lines li {
    display: flex; align-items: center; gap: 10px;
    font-size: 19px; color: var(--ink-soft); line-height: 1.45;
  }
  .contact__lines svg { width: 16px; height: 16px; flex: none; }

  .base-rule {
    position: absolute; left: 0; right: 0; top: 375px; height: 3px; background: var(--ink);
  }
  .base-band {
    position: absolute; left: 0; right: 0; bottom: 0; height: 33px; background: var(--accent-red);
  }

  .brand-row {
    position: absolute; left: 0; right: 0; top: 186px;
    display: flex; justify-content: center; align-items: center; gap: 34px;
  }
  .brand { display: flex; align-items: center; gap: 8px; font-size: 26px; font-weight: 700; }
  .brand--fen { color: var(--card-white); }
  .brand--tava { color: var(--brand-grey); }
  .brand--elm { color: var(--card-white); }
  .brand--grit { color: var(--brand-red); }
  .brand__circle { width: 26px; height: 26px; border: 3px solid var(--brand-grey); border-radius: 50%; }
  .brand__square { width: 26px; height: 26px; background: var(--brand-violet); }
  .brand__square--red { background: var(--brand-red); }

  .back-url {
    position: absolute; left: 0; right: 0; top: 336px; text-align: center;
    color: var(--card-white); font-size: 21px; font-style: italic; letter-spacing: 10px;
  }
</style>
</head>
<body>
  <section class="card card--front">
    <div class="company-mark">
      <span class="company-mark__square"></span>
      <span class="company-mark__name">Fen Athletics</span>
    </div>
    <div class="divider"></div>
    <div class="contact">
      <p class="contact__name">Leo Pemberton-Hale</p>
      <p class="contact__role">Operations Manager</p>
      <p class="contact__address">Kestrel Yard, Lowfield<br>Marlow Vale, ZZ9 4QT</p>
      <ul class="contact__lines">
        <li>
          <svg viewBox="0 0 16 16" aria-hidden="true"><path fill="#e3202a" d="M3.5 1.5l2.5 3-1.6 1.6c.8 1.8 2.3 3.3 4.1 4.1L10.1 8.6l3 2.5-1.4 2.8C6.3 13.6 2.4 9.7 1 4.3z"/></svg>
          (+44) 1632 960 418
        </li>
        <li>
          <svg viewBox="0 0 16 16" aria-hidden="true"><rect x="1" y="3.5" width="14" height="9.5" fill="#e3202a"/><path d="M1.5 4l6.5 5 6.5-5" fill="none" stroke="#fff" stroke-width="1.2"/></svg>
          leo@fenathletics.co.uk
        </li>
        <li>
          <svg viewBox="0 0 16 16" aria-hidden="true"><circle cx="8" cy="8" r="7" fill="#e3202a"/><path d="M1 8h14M8 1c-3 3-3 11 0 14M8 1c3 3 3 11 0 14" fill="none" stroke="#fff" stroke-width="1"/></svg>
          www.fenathletics.co.uk
        </li>
      </ul>
    </div>
    <div class="base-rule"></div>
    <div class="base-band"></div>
  </section>

  <section class="card card--back">
    <div class="brand-row">
      <span class="brand brand--fen">Fen</span>
      <span class="brand brand--tava"><span class="brand__circle"></span>TavaPuni</span>
      <span class="brand brand--elm"><span class="brand__square"></span>ElmStretch</span>
      <span class="brand brand--grit"><span class="brand__square brand__square--red"></span>Grit and Rain</span>
    </div>
    <p class="back-url">www.fenathletics.co.uk</p>
  </section>
</body>
</html>
```